Fitness Equipment & Service

I want to make the card eye catching and fun. We are called Corvane Motion Limited and we are based in Wales. We sell, install and service all types of fitness equipment from Skipping ropes, right through the Dumbbells, Kettle bells and Barbells through to state of the art Treadmills, Running Machines and Strength Equipment. We also design and install changing room furniture and lockers.

TYPOGRAPHY
We would like to use Futrura. Futura has an appearance of efficiency and forwardness. The typeface is derived
from simple geometric forms (near-perfect circles, triangles and squares) and is based on strokes of
near-even weight, which are low in contrast. This is most visible in the almost perfectly round stroke of
the o, which is nonetheless slightly ovoid.
The lowercase has tall ascenders, which rise above the cap line. The uppercase
characters present proportions similar to those of classical Roman capitals.

TYPOGRAPHIC CONSIDERATIONS
No Strike though
No Horizontal Scaling
No Drop Shadows
No Effects
Never use less than 120% Leading

OUR CORPORATE COLOURS
BRAND GUIDELINES
We were thinking that our primary colour palette consists of the Acid Green (Pantone 382) and Process Black.

We work closely with tquarly Ltd and would like to include their name on the card somewhere. I have attached images of the other brands that we work with as an idea or the small icons I have included that illustrate what we do?. I have very kindly been given permission to use any of the images off the files that I have included below, so I hope these help. I will include these below. I would be open to suggestions if it made the card more striking Can you do it?
Updates

Hi All, Just wanted to add a few thoughts but you are the guys with the creative visions (thats why are here) We are based in Wales, UK and we would be open to lots of different ideas on a theme but must be eye catching, Bold and FUN. If you can or think that the Welsh or any dragon could be put in there then go for it (its not a must have) We have also added some ideas for colour but again its over to you!! GO FOR IT ! Thanks and look forward to your visions! Owen

Hi All, Just thought I would sen through the contact details that need to be on the card. (if you want to play around with icons instead of the wording twitter, Facebook, go for it): Corvane Motion Limited Owen Pritchard Managing Director Mob: +44 (0)7582 913 406 e-mail: sales@corvanemotion.co.uk Web: Corvanemotion.co.uk twitter: @motionLetterbin Facebook: Corvane Motion Limited

```html
<!DOCTYPE html>
<html lang="en">
<head>
<meta charset="utf-8">
<title>Corvane Motion Limited – Business Card</title>
<link rel="stylesheet" href="https://fonts.googleapis.com/css2?family=Open+Sans:wght@400;600;700&display=swap">
<style>
  :root {
    --page-bg: #e9e6e1;
    --card-bg: #ffffff;
    --acid-green: #c4d600;
    --process-black: #1a1a1a;
    --text-grey: #3d3d3d;
    --subtle-grey: #5a5a5a;
  }
  * { margin: 0; padding: 0; box-sizing: border-box; }
  html, body {
    width: 1200px; height: 902px; overflow: hidden;
    background: var(--page-bg);
    font-family: "Open Sans", Arial, sans-serif;
  }
  .business-card {
    position: absolute; left: 75px; top: 151px;
    width: 1050px; height: 600px;
    background: var(--card-bg);
    overflow: hidden;
    box-shadow: 0 6px 18px rgba(0,0,0,0.18);
  }
  .card-swoosh { position: absolute; inset: 0; width: 100%; height: 100%; }
  .holder { position: absolute; left: 62px; top: 92px; }
  .holder-name {
    color: var(--process-black); font-weight: 700; font-size: 46px; line-height: 1.2;
  }
  .holder-title {
    color: var(--subtle-grey); font-size: 26px; line-height: 1.2;
  }
  .contact-list {
    position: absolute; left: 62px; top: 262px;
    list-style: none;
  }
  .contact-item {
    display: flex; align-items: center; gap: 18px;
    font-size: 25px; line-height: 1.6; color: var(--text-grey);
  }
  .contact-icon {
    width: 22px; height: 22px; flex: none;
    background: var(--acid-green); border-radius: 2px;
    display: flex; align-items: center; justify-content: center;
  }
  .contact-icon svg { width: 14px; height: 14px; }
  .brand-block {
    position: absolute; right: 60px; top: 30px;
    width: 300px;
    display: flex; flex-direction: column; align-items: center; gap: 14px;
  }
  .brand-disc {
    width: 150px; height: 150px; border-radius: 50%;
    background: var(--process-black);
  }
  .brand-name {
    color: var(--process-black); font-weight: 700; font-size: 22px; line-height: 1.2;
    white-space: nowrap; text-align: center;
  }
</style>
</head>
<body>
  <div class="business-card">
    <svg class="card-swoosh" viewBox="0 0 1050 600" preserveAspectRatio="none" aria-hidden="true">
      <path d="M0 540 C 420 560, 820 470, 1050 250 L1050 600 L0 600 Z" fill="var(--acid-green)"/>
      <path d="M0 556 C 430 576, 830 492, 1050 276 L1050 600 L0 600 Z" fill="#ffffff"/>
      <path d="M0 572 C 440 590, 840 510, 1050 296 L1050 600 L0 600 Z" fill="var(--process-black)"/>
    </svg>

    <div class="holder">
      <div class="holder-name">Owen Pritchard</div>
      <div class="holder-title">Managing Director</div>
    </div>

    <ul class="contact-list">
      <li class="contact-item">
        <span class="contact-icon"><svg viewBox="0 0 14 14"><rect x="4" y="1" width="6" height="12" rx="1" fill="var(--process-black)"/></svg></span>
        +44 (0)7582 913 406
      </li>
      <li class="contact-item">
        <span class="contact-icon"><svg viewBox="0 0 14 14"><rect x="1" y="3" width="12" height="8" fill="var(--process-black)"/><path d="M1 3 L7 8 L13 3" stroke="var(--acid-green)" fill="none"/></svg></span>
        sales@corvanemotion.co.uk
      </li>
      <li class="contact-item">
        <span class="contact-icon"><svg viewBox="0 0 14 14"><circle cx="7" cy="7" r="5.5" fill="none" stroke="var(--process-black)" stroke-width="1.5"/><path d="M1.5 7 H12.5 M7 1.5 V12.5" stroke="var(--process-black)"/></svg></span>
        Corvanemotion.co.uk
      </li>
      <li class="contact-item">
        <span class="contact-icon"></span>
        @motionLetterbin
      </li>
      <li class="contact-item">
        <span class="contact-icon"></span>
        Corvane Motion Limited
      </li>
    </ul>

    <div class="brand-block">
      <div class="brand-disc"></div>
      <div class="brand-name">Corvane Motion Limited</div>
    </div>
  </div>
</body>
</html>
```